Design a product reviews website

We need a website design and simple logo for the brand Venlotix.com. The website will provide reviews of technology products and services. The brand and website should be approachable but should also be trustworthy and high quality. The deliverable should be designs, specs and assets that I can provide to a development team to build the website.

Target Market(s)

People researching products to buy.

Industry/Entity Type

Product

Logo Text

Venlotix.com

Number of Pages Required

5+ page

Font styles to use
Sans Serif

Colors
0492cd
0355a3
3176b5
33a6d7
85cae6
85abd2
cedeed
cee9f5

Requirements
Must have
• - Designs for the Homepage, Category and Article pages.
• - Designs for web and mobile.
• - Designs details for the engineering team to use for development.
• - I'm open to other colors than the preferences I chose but I'm more likely to like blues, greys and blacks.

```html
<!DOCTYPE html>
<html lang="en">
<head>
<meta charset="utf-8">
<title>Venlotix.com – Product Reviews</title>
<link href="https://fonts.googleapis.com/css2?family=Raleway:wght@400;500;600;700&display=swap" rel="stylesheet">
<style>
:root{
  --blue:#34a3d8;
  --blue-dark:#0492cd;
  --ink:#1e1e1e;
  --text:#333;
  --muted:#666;
  --line:#e2e2e2;
  --soft:#f2f2f2;
  --white:#fff;
  --footer:#111;
}
*{box-sizing:border-box;margin:0;padding:0}
html,body{width:1200px;height:2214px;overflow:hidden;background:var(--white);font-family:'Raleway',sans-serif;color:var(--text)}
.page{position:relative;width:1200px;height:2214px}

/* hero */
.hero{position:absolute;left:0;top:0;width:1200px;height:453px;
  background:linear-gradient(160deg,#3a3a3a 0%,#262626 35%,#4a4a4a 60%,#2a2a2a 100%)}
.hero-shade{position:absolute;inset:0;background:radial-gradient(ellipse at 55% 60%,rgba(120,120,120,.35),rgba(0,0,0,.1) 70%)}
.brand{position:absolute;left:99px;top:28px;display:flex;align-items:center;gap:8px;color:var(--white);font-weight:600;font-size:24px;letter-spacing:.3px}
.brand-mark{width:20px;height:20px;background:var(--blue);border-radius:50%}
.menu-btn{position:absolute;left:1065px;top:29px;width:34px;height:34px;border:2px solid var(--white);border-radius:50%}
.menu-btn svg{position:absolute;left:8px;top:9px}
.hero-title{position:absolute;left:0;top:132px;width:1200px;text-align:center;color:var(--white);font-weight:400;font-size:35px;line-height:36px}
.hero-sub{position:absolute;left:0;top:217px;width:1200px;text-align:center;color:#eee;font-size:14px}
.search{position:absolute;left:428px;top:261px;width:284px;height:33px;border:2px solid var(--white);border-radius:17px;background:rgba(255,255,255,.12);color:#ddd;font-size:12px;padding:7px 20px}
.search-btn{position:absolute;left:727px;top:260px;width:44px;height:35px;border-radius:18px;background:var(--blue);border:2px solid var(--white)}
.search-btn svg{position:absolute;left:14px;top:9px}

/* sidebar */
.sidebar{position:absolute;left:99px;top:505px;width:230px}
.side-head{background:var(--blue);color:var(--white);text-align:center;font-weight:600;font-size:17px;height:41px;line-height:41px;letter-spacing:.5px}
.cat-list{list-style:none;border-left:1px solid var(--line);border-right:1px solid var(--line)}
.cat-list li{height:36px;line-height:36px;border-bottom:1px solid var(--line);font-size:13px;color:#444;padding-left:38px;position:relative}
.cat-list li::before{content:"›";position:absolute;left:16px;color:#aaa;font-size:15px}
.cat-list li.active{background:var(--soft)}
.side-card{position:absolute;left:0;width:230px;border:1px solid var(--line);box-shadow:0 1px 3px rgba(0,0,0,.12);padding:9px 9px 0}
.side-card .side-head{height:43px;line-height:43px;font-size:17px;margin-bottom:9px}

/* main */
.main{position:absolute;left:365px;top:505px;width:736px}
.tabs{position:relative;height:35px;border-bottom:2px solid var(--blue)}
.tab{position:absolute;top:0;height:34px;line-height:34px;font-size:13px;font-weight:600}
.tab-active{left:0;width:187px;background:var(--blue);color:var(--white);text-align:center;letter-spacing:.5px}
.tab-plain{left:211px;color:#333;letter-spacing:.4px}
.tab-div{position:absolute;left:367px;top:10px;width:1px;height:18px;background:#ccc}
.tab-arrows{position:absolute;right:0;top:4px;display:flex;gap:6px}
.tab-arrows span{width:20px;height:20px;border:1px solid #999;display:block;position:relative}
.tab-arrows svg{position:absolute;left:3px;top:5px}

.card{position:absolute;width:341px;border:1px solid var(--line);box-shadow:0 1px 3px rgba(0,0,0,.12);padding:9px 9px 0;background:var(--white)}
.photo{position:relative;width:100%}
.tags{position:absolute;right:9px;top:9px;display:flex;flex-direction:column;align-items:flex-end;gap:7px}
.tag{width:86px;height:23px;line-height:23px;border-radius:12px;text-align:center;font-size:10px;font-weight:600;letter-spacing:.4px}
.tag-home{background:var(--white);color:var(--blue)}
.tag-speakers{background:var(--blue);color:var(--white)}
.card-title{font-weight:600;font-size:15.5px;color:var(--ink);margin:23px 0 0 2px}
.meta{display:flex;width:236px;height:27px;border:1px solid var(--line);margin:13px 0 19px 2px;font-size:12px;color:#444}
.meta .author{display:flex;align-items:center;gap:9px;flex:1;border-right:1px solid var(--line)}
.avatar{width:26px;height:26px;background:linear-gradient(135deg,#b98a6e,#6a4c3e)}
.meta .date{width:96px;text-align:center;line-height:25px}
.side-card .card-title{margin-top:17px}
.side-card .meta{width:210px;margin-left:0}
.side-card .meta .date{width:88px}

.img-speaker{background:linear-gradient(180deg,#2b2b2b,#5a5a5a 70%,#8a8a8a)}
.img-teal{background:linear-gradient(160deg,#6e5a48,#b9a590 40%,#4fb2b2 70%,#d9d2c8)}
.img-camera{background:linear-gradient(170deg,#3e4a52,#6f7a80 45%,#8a6a4e 100%)}
.img-kitchen{background:linear-gradient(180deg,#e8ecee,#cfd4d4 50%,#b8b0a4)}
.img-radio{background:linear-gradient(180deg,#6a3a28,#e4e2e4 50%,#c7a27a)}
.img-black{background:linear-gradient(180deg,#3a3a3a,#151515)}

.load-more{position:absolute;left:534px;top:2093px;width:130px;height:41px;border-radius:21px;background:var(--blue);border:2px solid var(--blue-dark);color:var(--white);font-size:12px;font-weight:600;text-align:center;line-height:37px;letter-spacing:.5px}

.footer{position:absolute;left:0;top:2162px;width:1200px;height:52px;background:var(--footer);color:#ddd;font-size:13px;text-align:center;line-height:52px}
.footer strong{color:var(--white)}
</style>
</head>
<body>
<div class="page">

  <header class="hero">
    <div class="hero-shade" role="img" aria-label="Photo of a silver desktop computer and keyboard on a desk"></div>
    <div class="brand"><span class="brand-mark"></span>Venlotix.com</div>
    <div class="menu-btn"><svg width="14" height="12" viewBox="0 0 14 12"><path d="M0 1h14M0 6h14M0 11h14" stroke="#fff" stroke-width="2"/></svg></div>
    <h1 class="hero-title">The Best Product And Services Reviews<br>And Rankings</h1>
    <p class="hero-sub">Simply dummy text of the printing and typesetting industry.</p>
    <div class="search">Search...</div>
    <div class="search-btn"><svg width="14" height="14" viewBox="0 0 14 14"><circle cx="6" cy="6" r="4.2" fill="none" stroke="#fff" stroke-width="2"/><path d="M9 9l4 4" stroke="#fff" stroke-width="2.2"/></svg></div>
  </header>

  <aside class="sidebar">
    <div class="side-head">CATEGORIES</div>
    <ul class="cat-list">
      <li>APPLIANCES</li>
      <li class="active">COMPUTERS</li>
      <li>ELECTRONIC</li>
      <li>HOME SECURITY</li>
      <li>MOBILE</li>
      <li>SMART HOME</li>
      <li>SOFTWARE</li>
    </ul>

    <div class="side-card" style="top:319px">
      <div class="side-head">POPULAR</div>
      <div class="photo img-radio" style="height:177px" role="img" aria-label="White bedside radio with pink and blue buttons"></div>
      <h3 class="card-title">Lorem Ipsum Dolor</h3>
      <div class="meta"><div class="author"><span class="avatar"></span>Day Smith</div><div class="date">Aug 11, 2016</div></div>
    </div>

    <div class="side-card" style="top:686px">
      <div class="photo img-kitchen" style="height:376px" role="img" aria-label="Bright kitchen with bar stools at a counter">
        <div class="tags"><span class="tag tag-home">HOME</span><span class="tag tag-speakers">SPEAKERS</span></div>
      </div>
      <h3 class="card-title">Lorem Ipsum Dolor</h3>
      <div class="meta"><div class="author"><span class="avatar"></span>Day Smith</div><div class="date">Aug 11, 2016</div></div>
    </div>

    <div class="side-card" style="top:1200px">
      <div class="photo img-black" style="height:250px" role="img" aria-label="Black fabric speaker front">
        <div class="tags"><span class="tag tag-home">HOME</span></div>
      </div>
      <h3 class="card-title">Lorem Ipsum Dolor</h3>
      <div class="meta"><div class="author"><span class="avatar"></span>Day Smith</div><div class="date">Aug 11, 2016</div></div>
    </div>
  </aside>

  <main class="main">
    <nav class="tabs">
      <span class="tab tab-active">LATEST COMPARISONS</span>
      <span class="tab tab-plain">PRODUCT ARTICLE</span>
      <span class="tab-div"></span>
      <div class="tab-arrows">
        <span><svg width="12" height="8" viewBox="0 0 12 8"><path d="M12 4H1M4 1L1 4l3 3" fill="none" stroke="#888"/></svg></span>
        <span><svg width="12" height="8" viewBox="0 0 12 8"><path d="M0 4h11M8 1l3 3-3 3" fill="none" stroke="#888"/></svg></span>
      </div>
    </nav>
  </main>

  <!-- left column -->
  <article class="card" style="left:365px;top:565px">
    <div class="photo img-speaker" style="height:230px" role="img" aria-label="Cylindrical smart speaker on a desk">
      <div class="tags"><span class="tag tag-home">HOME</span><span class="tag tag-speakers">SPEAKERS</span></div>
    </div>
    <h3 class="card-title">The Nuvora Hub...One Of Our Essentials</h3>
    <div class="meta"><div class="author"><span class="avatar"></span>Dayne Smith</div><div class="date">Aug 11, 2016</div></div>
  </article>

  <article class="card" style="left:365px;top:933px">
    <div class="photo img-camera" style="height:334px" role="img" aria-label="Video camera with a fluffy microphone on a wooden desk">
      <div class="tags"><span class="tag tag-home">HOME</span></div>
    </div>
    <h3 class="card-title">The Nuvora Hub...One Of Our Essentials</h3>
    <div class="meta"><div class="author"><span class="avatar"></span>Dayne Smith</div><div class="date">Aug 11, 2016</div></div>
  </article>

  <article class="card" style="left:365px;top:1404px">
    <div class="photo img-teal" style="height:230px" role="img" aria-label="Teal portable speaker on a table">
      <div class="tags"><span class="tag tag-speakers">SPEAKERS</span></div>
    </div>
    <h3 class="card-title">The Nuvora Hub...One Of Our Essentials</h3>
    <div class="meta"><div class="author"><span class="avatar"></span>Dayne Smith</div><div class="date">Aug 11, 2016</div></div>
  </article>

  <article class="card" style="left:365px;top:1771px">
    <div class="photo img-speaker" style="height:182px" role="img" aria-label="Cylindrical smart speaker on a desk">
      <div class="tags"><span class="tag tag-home">HOME</span><span class="tag tag-speakers">SPEAKERS</span></div>
    </div>
    <h3 class="card-title">The Nuvora Hub...One Of Our Essentials</h3>
    <div class="meta"><div class="author"><span class="avatar"></span>Dayne Smith</div><div class="date">Aug 11, 2016</div></div>
  </article>

  <!-- right column -->
  <article class="card" style="left:734px;top:567px">
    <div class="photo img-teal" style="height:334px" role="img" aria-label="Teal portable speaker on a table">
      <div class="tags"><span class="tag tag-home">HOME</span></div>
    </div>
    <h3 class="card-title">The Nuvora Hub...One Of Our Essentials</h3>
    <div class="meta"><div class="author"><span class="avatar"></span>Dayne Smith</div><div class="date">Aug 11, 2016</div></div>
  </article>

  <article class="card" style="left:734px;top:1036px">
    <div class="photo img-kitchen" style="height:435px" role="img" aria-label="Bright kitchen with bar stools at a counter">
      <div class="tags"><span class="tag tag-home">HOME</span><span class="tag tag-speakers">SPEAKERS</span></div>
    </div>
    <h3 class="card-title">The Nuvora Hub...One Of Our Essentials</h3>
    <div class="meta"><div class="author"><span class="avatar"></span>Dayne Smith</div><div class="date">Aug 11, 2016</div></div>
  </article>

  <article class="card" style="left:734px;top:1618px">
    <div class="photo img-camera" style="height:335px" role="img" aria-label="Video camera with a fluffy microphone on a wooden desk">
      <div class="tags"><span class="tag tag-speakers">SPEAKERS</span></div>
    </div>
    <h3 class="card-title">The Nuvora Hub...One Of Our Essentials</h3>
    <div class="meta"><div class="author"><span class="avatar"></span>Dayne Smith</div><div class="date">Aug 11, 2016</div></div>
  </article>

  <div class="load-more">LOAD MORE</div>

  <footer class="footer">Copyright © 2016 <strong>VENLOTIX</strong> | All Rights Reserved.</footer>
</div>
</body>
</html>
```